Business Card Design

We provide services doing multiple jobs in the construction industry.Please note: The company name needs to be ROCK SOLID BUILDING SERVICESAttached logo was an example of what we wanted. Can you change up the colors?

Industry/Entity Type

Construction

Contact Information for Business Card

ROCK SOLID BUILDING SERVICES5401 HUDSON BEND RDAUSTIN, TX 78734(512)243-6854ROCKSOLIDBUILDINGSERVICES@GMAIL.COM

```html
<!DOCTYPE html>
<html lang="en">
<head>
<meta charset="utf-8">
<title>Pearlwood Framing Works – Business Card</title>
<link rel="stylesheet" href="https://fonts.googleapis.com/css2?family=Titillium+Web:wght@700&family=Arimo:wght@400&display=swap">
<style>
  :root {
    --backdrop-light: #8fb0cb;
    --backdrop-dark: #4d7191;
    --band-top: #2b2a66;
    --band-bottom: #0d1228;
    --panel-light: #b7cad8;
    --panel-mid: #9fb6c8;
    --panel-edge: #7f9cb4;
    --footer: #070509;
    --cream: #e9dfc6;
    --ink: #0b0d1a;
    --navy: #1f2350;
  }
  * { margin: 0; padding: 0; box-sizing: border-box; }
  html, body {
    width: 1200px;
    height: 902px;
    overflow: hidden;
  }
  body {
    background: radial-gradient(ellipse at 45% 55%, var(--backdrop-light) 0%, var(--backdrop-dark) 80%);
    position: relative;
  }
  .business-card {
    position: absolute;
    left: 100px;
    top: 165px;
    width: 1000px;
    height: 571px;
    display: flex;
    flex-direction: column;
    box-shadow: 0 12px 30px rgba(20, 40, 60, 0.35);
  }
  .card-header {
    height: 152px;
    background: linear-gradient(180deg, var(--band-top) 0%, var(--band-top) 45%, var(--band-bottom) 62%, var(--band-bottom) 100%);
    display: flex;
    align-items: center;
    justify-content: center;
  }
  .company-name {
    font-family: 'Titillium Web', sans-serif;
    font-weight: 700;
    font-size: 51px;
    letter-spacing: 1px;
    color: var(--cream);
  }
  .card-body {
    height: 355px;
    position: relative;
    background: linear-gradient(100deg, var(--panel-mid) 0%, var(--panel-light) 40%, var(--panel-mid) 75%, var(--panel-edge) 100%);
  }
  .brand-mark {
    position: absolute;
    left: 47px;
    top: 55px;
    width: 354px;
    height: 226px;
    display: flex;
    flex-direction: column;
    align-items: center;
    justify-content: center;
    font-family: 'Titillium Web', sans-serif;
    font-weight: 700;
    font-size: 44px;
    line-height: 1.05;
    color: var(--navy);
    text-align: center;
  }
  .contact-list {
    position: absolute;
    left: 447px;
    top: 150px;
    list-style: none;
    font-family: 'Arimo', sans-serif;
    font-size: 25px;
    color: var(--ink);
  }
  .contact-item {
    display: flex;
    align-items: center;
    height: 44px;
  }
  .contact-icon {
    width: 28px;
    height: 28px;
    margin-right: 16px;
    flex: none;
  }
  .card-footer {
    height: 64px;
    background: var(--footer);
    display: flex;
    align-items: center;
    padding-left: 206px;
  }
  .address {
    font-family: 'Arimo', sans-serif;
    font-size: 26px;
    color: var(--cream);
  }
</style>
</head>
<body>
  <div class="business-card">
    <header class="card-header">
      <h1 class="company-name">PEARLWOOD FRAMING WORKS</h1>
    </header>
    <section class="card-body">
      <div class="brand-mark">
        <span>PEARLWOOD</span>
        <span>FRAMING WORKS</span>
      </div>
      <ul class="contact-list">
        <li class="contact-item">
          <svg class="contact-icon" viewBox="0 0 28 28" aria-hidden="true">
            <rect width="28" height="28" fill="var(--navy)"/>
            <path d="M8 6c1-1 2-1 3 0l2 3c.5 1 .3 1.8-.5 2.5l-1 .8c.8 2 2.4 3.6 4.4 4.4l.8-1c.7-.8 1.5-1 2.5-.5l3 2c1 1 1 2 0 3l-1.2 1.2C18 24 5 11 6.8 7.2z" fill="var(--cream)"/>
          </svg>
          <span>(512)555-0193</span>
        </li>
        <li class="contact-item">
          <svg class="contact-icon" viewBox="0 0 28 28" aria-hidden="true">
            <rect width="28" height="28" fill="var(--navy)"/>
            <rect x="5" y="8" width="18" height="13" fill="var(--cream)"/>
            <path d="M5 8l9 7 9-7" fill="none" stroke="var(--navy)" stroke-width="1.6"/>
          </svg>
          <span>Pearlwoodframingworks@mailnest.example</span>
        </li>
      </ul>
    </section>
    <footer class="card-footer">
      <p class="address">7732 Fernglen Pass LN Austin, TX 78734</p>
    </footer>
  </div>
</body>
</html>
```